postcard for Real Estate Agent that sells homes for less than any other agents

My company sells houses for a fraction of what others charge. I have most of the verbiage but I am open to ideas.
Our post card will be 6.25 x 9
We need an image that goes with our words and draws people to take a look
We are playful at the same time very serious about the money we will save our clients. In the past our message has been received as too good to be true. Our old message was "save $6000* when you list with us" We think the "*" was causing people to think their was a catch. Other agents will tell people that we will not do what they will do and that is why they must charge more. We are a full service agency and we will generally do everything that other agents will do and in many cases we will do more than other agents. We are changing this industry and need our message to get to every person that is thinking of selling their home

Target Market(s)

People who want to list their home for sale

Industry/Entity Type

Real Estate Agent

Requirements
Must have
• Image that makes people read the message

```html
<!DOCTYPE html>
<html lang="en">
<head>
<meta charset="utf-8">
<title>Keystone Realty Postcard</title>
<link rel="stylesheet" href="https://fonts.googleapis.com/css2?family=Arimo:wght@400;700&display=swap">
<style>
  :root {
    --navy: #1d3f73;
    --navy-deep: #173563;
    --yellow: #fff200;
    --sky: #7ea6cc;
    --white: #ffffff;
    --ink: #1f3d6e;
  }
  * { margin: 0; padding: 0; box-sizing: border-box; }
  html, body { width: 1200px; height: 800px; overflow: hidden; background: var(--white); }
  body { font-family: "Arimo", Arial, sans-serif; }
  .postcard { position: relative; width: 1200px; height: 800px; overflow: hidden; background: var(--white); }
  .hero { position: absolute; left: 0; top: 0; width: 1200px; height: 600px; }
  .headline { position: absolute; left: 52px; top: 44px; color: var(--white); font-weight: 700; text-shadow: 2px 3px 0 rgba(0,0,0,.55); }
  .headline .line { display: block; font-size: 38px; line-height: 42px; letter-spacing: -0.3px; }
  .headline .shout { display: block; color: var(--yellow); font-size: 66px; line-height: 74px; letter-spacing: 0.5px; }
  .offer { position: absolute; left: 63px; top: 284px; color: var(--sky); font-weight: 700; font-size: 30px; line-height: 36px; }
  .offer .amount { color: var(--white); }
  .uses { position: absolute; left: 64px; top: 366px; display: grid; grid-template-columns: 220px 220px; row-gap: 4px; list-style: none; }
  .uses li { color: var(--white); font-weight: 700; font-size: 17px; line-height: 22px; padding-left: 18px; position: relative; }
  .uses li::before { content: ""; position: absolute; left: 0; top: 6px; border-left: 9px solid var(--sky); border-top: 5px solid transparent; border-bottom: 5px solid transparent; }
  .promise { position: absolute; left: 66px; top: 514px; color: var(--yellow); font-weight: 700; font-size: 27px; line-height: 34px; }
  .brand { position: absolute; left: 92px; top: 672px; display: flex; align-items: center; gap: 12px; }
  .brand .mark { width: 34px; height: 34px; background: var(--navy); }
  .brand .name { color: var(--navy); font-weight: 700; font-size: 30px; }
  .contact { position: absolute; left: 500px; top: 616px; width: 600px; text-align: center; font-weight: 700; }
  .contact .call { color: var(--ink); font-size: 34px; line-height: 40px; }
  .contact .phone { color: var(--sky); font-size: 86px; line-height: 90px; letter-spacing: -1px; }
  .contact .web { color: var(--ink); font-size: 33px; line-height: 40px; }
</style>
</head>
<body>
<div class="postcard">
  <svg class="hero" viewBox="0 0 1200 600" width="1200" height="600">
    <defs>
      <linearGradient id="scene" x1="0" y1="0" x2="0" y2="1">
        <stop offset="0" stop-color="#b9b2a6"/>
        <stop offset="0.4" stop-color="#8d4a38"/>
        <stop offset="0.55" stop-color="#6f8a3c"/>
        <stop offset="1" stop-color="#4f7a22"/>
      </linearGradient>
    </defs>
    <rect width="1200" height="600" fill="var(--navy)"/>
    <polygon points="800,0 1200,0 1200,600 548,600" fill="url(#scene)" role="img" aria-label="Photo of a stressed man in a suit sitting on a lawn beside a For Sale sign in front of a house"/>
    <polygon points="796,0 806,0 554,600 544,600" fill="var(--white)"/>
  </svg>

  <h1 class="headline">
    <span class="line">You’d have to be</span>
    <span class="shout">Bat $#@T CRAZY</span>
    <span class="line">to give an agent $6000.00</span>
    <span class="line">To put a sign in your yard.</span>
  </h1>

  <p class="offer">Look at what you<br>can do with <span class="amount">$6000.00</span></p>

  <ul class="uses">
    <li>Give it to your Kids</li><li>Build a fence</li>
    <li>Build a deck</li><li>Buy new clothes</li>
    <li>Landscape</li><li>Take a Vacation</li>
    <li>Pay off your car</li><li>Pay off student loan</li>
    <li>Buy New Carpet</li><li>pgrade Appliances</li>
  </ul>

  <p class="promise">FULL SERVICE AGENCY AT A<br>FRACTION OF THE COST</p>

  <div class="brand">
    <span class="mark"></span>
    <span class="name">Keystone Realty</span>
  </div>

  <div class="contact">
    <p class="call">Call Dale or Marcus at</p>
    <p class="phone">555.204.7319</p>
    <p class="web">www.DaleHomeGroup.com</p>
  </div>
</div>
</body>
</html>
```